Business Card Design Project

We are a construction company in Orange County, CA. We need a two sided business card. We would like the back to be our logo with web URL. Front should included Name, title, address, phone, fax and email address.

our address is
627 West Dorrance Blvd, Suite 308
Larkmont, CA 92718

Our logo files are attached.

Construction

```html
<!DOCTYPE html>
<html lang="en">
<head>
<meta charset="utf-8">
<title>Tarnwell Business Card</title>
<link href="https://fonts.googleapis.com/css2?family=PT+Sans:wght@400;700&display=swap" rel="stylesheet">
<style>
  :root {
    --backdrop: #e9e6e1;
    --card: #ffffff;
    --card-edge: #3a3a3a;
    --brand-blue: #174a7e;
    --ink-black: #0a0a0a;
    --text-grey: #3c3c3c;
    --url-grey: #555555;
  }
  * { margin: 0; padding: 0; box-sizing: border-box; }
  html, body {
    width: 1200px; height: 410px; overflow: hidden;
    background: var(--backdrop);
    font-family: "PT Sans", Arial, sans-serif;
  }
  .canvas { position: relative; width: 1200px; height: 410px; }

  .card {
    position: absolute;
    background: var(--card);
    border: 1px solid var(--card-edge);
    border-radius: 22px;
    overflow: hidden;
  }
  .card--front { left: 47px; top: 53px; width: 540px; height: 307px; }
  .card--back  { left: 617px; top: 55px; width: 524px; height: 299px; }

  .edge-band { position: absolute; right: 0; top: 0; width: 41px; height: 100%; }

  .brand-name {
    position: absolute; left: 0;
    text-align: center; color: var(--brand-blue);
    font-weight: 700;
    font-size: 66px;
    line-height: 70px;
    letter-spacing: 1px;
  }
  .card--front .brand-name { width: 486px; top: 50px; }
  .card--back .brand-name  { width: 524px; top: 98px; }

  .person {
    position: absolute; left: 0; width: 500px; top: 176px;
    text-align: center; color: var(--brand-blue); font-size: 18px;
  }
  .person__name { font-weight: 700; }

  .contact {
    position: absolute; left: 0; width: 500px;
    text-align: center; color: var(--text-grey); font-size: 13.5px;
  }
  .contact--row1 { top: 211px; }
  .contact--row2 { top: 229px; }
  .contact--address { top: 259px; font-size: 14px; }
  .contact__item { display: inline-flex; align-items: center; margin: 0 3px; }
  .contact__icon { width: 11px; height: 11px; margin-right: 5px; fill: var(--text-grey); }

  .web-address {
    position: absolute; left: 0; width: 524px; top: 202px;
    text-align: center; color: var(--url-grey);
    font-size: 14px; letter-spacing: 2.6px;
  }
</style>
</head>
<body>
<div class="canvas">

  <section class="card card--front">
    <svg class="edge-band" viewBox="0 0 41 307" preserveAspectRatio="none" aria-hidden="true">
      <polygon points="0,0 41,0 41,92 0,122" fill="var(--brand-blue)"/>
      <polygon points="0,122 41,92 41,307 0,307" fill="var(--ink-black)"/>
    </svg>

    <p class="brand-name">TARNWELL</p>

    <p class="person"><span class="person__name">Your Name,</span> Title</p>

    <p class="contact contact--row1">
      <span class="contact__item">
        <svg class="contact__icon" viewBox="0 0 12 12" aria-hidden="true"><path d="M2.5 0.5 L4.5 0.5 L5.2 3 L3.8 4.2 C4.5 5.8 6.2 7.5 7.8 8.2 L9 6.8 L11.5 7.5 L11.5 9.5 C11.5 10.8 10.5 11.5 9.5 11.5 C4.5 11 1 7.5 0.5 2.5 C0.5 1.5 1.2 0.5 2.5 0.5 Z"/></svg>01-555-0147
      </span>
      <span class="contact__item">
        <svg class="contact__icon" viewBox="0 0 12 12" aria-hidden="true"><rect x="3" y="0.5" width="6" height="3.5"/><path d="M0.5 5 H11.5 V10 H9.5 V8 H2.5 V10 H0.5 Z"/><rect x="3" y="9" width="6" height="2.5"/></svg>01-555-0148
      </span>
    </p>
    <p class="contact contact--row2">
      <span class="contact__item">
        <svg class="contact__icon" viewBox="0 0 12 12" aria-hidden="true"><path d="M0.5 2.5 H11.5 V9.5 H0.5 Z M0.5 2.5 L6 6.5 L11.5 2.5" stroke="#fff" stroke-width="0.8"/></svg>info@tarnwellbuild.com
      </span>
      <span class="contact__item">
        <svg class="contact__icon" viewBox="0 0 12 12" aria-hidden="true"><circle cx="6" cy="6" r="5.5"/><path d="M0.5 6 H11.5 M6 0.5 C3.5 3 3.5 9 6 11.5 M6 0.5 C8.5 3 8.5 9 6 11.5" stroke="#fff" stroke-width="0.8" fill="none"/></svg>www.tarnwellbuild.com
      </span>
    </p>
    <p class="contact contact--address">627 West Dorrance Blvd, Suite 308, Larkmont, CA&nbsp; 92718</p>
  </section>

  <section class="card card--back">
    <p class="brand-name">TARNWELL</p>
    <p class="web-address">www.tarnwellbuild.com</p>
  </section>

</div>
</body>
</html>
```